Post Disaster Temporary Housing Literature Review poster

Wanting a poster design for two Emergency Management conferences we have coming up. The information to be included in the poster is capturing the purpose, findings and recommendations from a post disaster temporary housing literature review looking at “What should government consider in order to improve planning and decision making for accommodation needs after a disaster, and to support people’s transition to stable housing?”
I’d like to enhance the visual appeal through including relevant images or graphic. I am also open to reducing the text if needed.
The government group I work with focuses on the social and human side of disaster recovery so keen for any images to reflect the human aspect and not focus solely on disasters or housing.
Government and NGO's

```html
<!DOCTYPE html>
<html lang="en">
<head>
<meta charset="utf-8">
<title>Post Disaster Temporary Housing Conference</title>
<link href="https://fonts.googleapis.com/css2?family=Lato:wght@400;700;900&display=swap" rel="stylesheet">
<style>
  :root {
    --orange: #f47b20;
    --orange-deep: #d9620f;
    --ink: #1b1b1b;
    --text: #4a4a4a;
    --paper: #f1f1f1;
    --photo-dark: #4e4e4e;
    --photo-mid: #7d7d7d;
    --photo-light: #b3b3b3;
    --white: #ffffff;
  }
  * { margin: 0; padding: 0; box-sizing: border-box; }
  html, body { width: 848px; height: 1200px; overflow: hidden; background: var(--paper); }
  body { font-family: 'Lato', sans-serif; color: var(--text); }
  .poster { position: relative; width: 848px; height: 1200px; background: var(--paper); overflow: hidden; }
  .hero { position: absolute; top: 0; left: 0; width: 848px; height: 630px; }
  .title { position: absolute; left: 209px; top: 437px; color: var(--white); font-weight: 900; }
  .title-kicker { font-size: 20px; letter-spacing: -0.3px; line-height: 1; }
  .title-main { font-size: 40px; letter-spacing: -1px; line-height: 1; margin-top: 6px; }
  .title-tail { font-size: 21px; line-height: 1; text-align: right; margin-top: 8px; letter-spacing: -0.3px; }
  .column { position: absolute; top: 660px; }
  .column-left { left: 62px; width: 354px; }
  .column-right { left: 436px; width: 370px; }
  .section-heading { font-size: 30px; font-weight: 900; color: var(--ink); letter-spacing: -0.8px; line-height: 1; }
  .section-heading .accent { color: var(--orange); }
  .body-copy { font-size: 12.6px; line-height: 18.9px; margin-top: 20px; }
  .body-copy + .body-copy { margin-top: 7px; }
  .research-question { width: 362px; font-size: 14.4px; font-weight: 700; color: var(--ink); line-height: 20.3px; margin-top: 20px; letter-spacing: -0.1px; }
  .research-question + .body-copy { margin-top: 18px; }
  .bullet-list { list-style: none; margin-top: 17px; }
  .bullet-list li { position: relative; padding-left: 18px; font-size: 12.6px; font-weight: 700; color: #2a2a2a; line-height: 26.6px; }
  .bullet-list li::before { content: ""; position: absolute; left: 0; top: 12px; width: 3px; height: 3px; border-radius: 50%; background: var(--orange); }
  .heading-recs { margin-top: 15px; }
  .recommendations { margin-top: 13px; }
  .recommendations li { font-weight: 400; color: var(--ink); font-size: 13px; }
  .footer { position: absolute; left: 0; top: 1137px; width: 848px; height: 63px; background: var(--orange); color: var(--white); display: flex; align-items: center; }
  .footer-item { display: flex; align-items: center; font-size: 17px; font-weight: 700; }
  .footer-date { margin-left: 62px; }
  .footer-date svg { margin-right: 13px; }
  .footer-divider { margin: 0 18px; font-size: 17px; }
  .footer-email svg { margin-right: 13px; }
  .footer-social { position: absolute; right: 50px; display: flex; align-items: center; font-size: 12px; font-weight: 700; }
  .footer-social .dot { width: 22px; height: 22px; border-radius: 50%; background: var(--white); margin-right: 6px; }
  .footer-code { position: absolute; right: 14px; font-size: 8px; font-weight: 400; }
</style>
</head>
<body>
<main class="poster">
  <svg class="hero" viewBox="0 0 848 630" width="848" height="630">
    <defs>
      <linearGradient id="photoTone" x1="0" y1="0" x2="1" y2="1">
        <stop offset="0" stop-color="var(--photo-mid)"/>
        <stop offset="0.35" stop-color="var(--photo-dark)"/>
        <stop offset="0.7" stop-color="var(--photo-mid)"/>
        <stop offset="1" stop-color="var(--photo-light)"/>
      </linearGradient>
      <radialGradient id="crewGlow" cx="0.45" cy="0.4" r="0.55">
        <stop offset="0" stop-color="var(--orange)" stop-opacity="0.45"/>
        <stop offset="1" stop-color="var(--orange)" stop-opacity="0"/>
      </radialGradient>
      <linearGradient id="bandTone" x1="0" y1="0" x2="1" y2="0">
        <stop offset="0" stop-color="var(--orange-deep)"/>
        <stop offset="0.5" stop-color="var(--orange)"/>
        <stop offset="1" stop-color="var(--orange-deep)"/>
      </linearGradient>
    </defs>
    <g role="img" aria-label="Photograph of rescue workers in orange uniforms and yellow helmets searching through the rubble of a collapsed building">
      <polygon points="0,0 848,0 848,627 0,515" fill="url(#photoTone)"/>
      <polygon points="0,0 848,0 848,627 0,515" fill="url(#crewGlow)"/>
    </g>
    <polygon points="0,366 120,380 260,420 420,415 600,440 760,455 848,470 848,627 0,515" fill="url(#bandTone)" opacity="0.95"/>
  </svg>

  <header class="title">
    <div class="title-kicker">POST DISASTER</div>
    <div class="title-main">TEMPORARY HOUSING</div>
    <div class="title-tail">CONFERENCE</div>
  </header>

  <section class="column column-left">
    <h2 class="section-heading">OUR <span class="accent">PURPOSE</span></h2>
    <p class="body-copy">There are currently significant challenges in supporting displaced people with timely and equitable access to emergency and temporary accommodation and assisting them on a path to stable housing in the aftermath of a disaster. This report seeks to support agencies and decision makers to formulate and implement appropriate approaches to post-disaster housing, factoring in the scale of a disaster and varying community cohorts.</p>
    <p class="body-copy">The central research question underpinning this report is:</p>
    <p class="research-question">What should government consider in order to improve planning and decision making for accommodation needs after a disaster, and to support people’s transition to stable housing?</p>
    <p class="body-copy">The full report was commissioned by the Community Recovery Advisory Group (CRAG) and undertaken by Helen Marsh and Daniel Okoro through the Southern Coast Institute of Technology (SCIT). The findings and recommendations may be utilised by stakeholders.</p>
  </section>

  <section class="column column-right">
    <h2 class="section-heading">OUR <span class="accent">FINDINGS</span></h2>
    <ul class="bullet-list findings">
      <li>Leading practice in disaster housing recovery</li>
      <li>Innovative approaches to temporary housing</li>
      <li>A decision-making framework for resilient housing recovery</li>
    </ul>
    <h2 class="section-heading heading-recs">RECOMMENDATIONS</h2>
    <ul class="bullet-list recommendations">
      <li>Terminology</li>
      <li>Principles</li>
      <li>National Principles</li>
      <li>Guidelines</li>
      <li>Capacity Building</li>
      <li>Funding</li>
      <li>Further Research</li>
      <li>Pilot Project</li>
      <li>Decision Making Framework</li>
      <li>Capturing Learnings</li>
    </ul>
  </section>

  <footer class="footer">
    <div class="footer-item footer-date">
      <svg width="16" height="16" viewBox="0 0 16 16" aria-hidden="true">
        <rect x="1" y="3" width="14" height="12" rx="1" fill="none" stroke="#fff" stroke-width="1.6"/>
        <line x1="1" y1="6.5" x2="15" y2="6.5" stroke="#fff" stroke-width="1.6"/>
        <line x1="4.5" y1="1" x2="4.5" y2="4" stroke="#fff" stroke-width="1.6"/>
        <line x1="11.5" y1="1" x2="11.5" y2="4" stroke="#fff" stroke-width="1.6"/>
      </svg>
      January 2024
    </div>
    <span class="footer-divider">|</span>
    <div class="footer-item footer-email">
      <svg width="17" height="13" viewBox="0 0 17 13" aria-hidden="true">
        <rect x="0" y="0" width="17" height="13" rx="1.5" fill="#fff"/>
        <polyline points="1,1.5 8.5,7.5 16,1.5" fill="none" stroke="var(--orange)" stroke-width="1.5"/>
      </svg>
      claire.hollis@recoveryhub.gov.au
    </div>
    <div class="footer-social"><span class="dot"></span>RecoveryHub</div>
    <div class="footer-code">C45</div>
  </footer>
</main>
</body>
</html>
```